Meridale Partners Website

Meridale Partners (MP) provide Analytics & Enterprise Performance Management (EPM) advisory & consultancy services. We are passionate about data and making a difference for our clients by working in partnership with them, helping them on their journey to becoming an Meridale Partner. We deliver insights which give our clients a competitive edge and a much deeper understanding of their organisation.

We need a website which shows who we are, what we do and how we do it.

www.meridale-partners.example is our very basic website at the moment. We want to completely revamp it with a corporate look

```html
<!DOCTYPE html>
<html lang="en">
<head>
<meta charset="utf-8">
<title>Meridale Partners</title>
<link href="https://fonts.googleapis.com/css2?family=Raleway:wght@400;500;600;700&family=Nunito+Sans:wght@400;600;700;800&display=swap" rel="stylesheet">
<style>
:root{
  --navy:#27475c;
  --ink:#2c3a44;
  --blue:#2f7bb4;
  --blue-bright:#2a8fd8;
  --pale:#eef4f8;
  --deep:#132b3a;
  --footer:#29506a;
  --orange:#f0a21a;
  --muted:#5c6870;
  --white:#ffffff;
}
*{box-sizing:border-box;margin:0;padding:0}
html,body{width:1200px;height:3919px;overflow:hidden}
body{position:relative;background:var(--white);font-family:"Nunito Sans",sans-serif;color:var(--ink)}
.abs{position:absolute}
.h-font{font-family:"Raleway",sans-serif}

/* header */
.site-header{position:absolute;left:0;top:0;width:1200px;height:78px;border-bottom:1px solid #e3e8ec;background:#fff}
.brand{position:absolute;display:flex;align-items:center;gap:12px}
.brand-dot{width:46px;height:46px;border-radius:50%;background:var(--navy)}
.brand-name{font-family:"Raleway",sans-serif;font-weight:700;font-size:19px;line-height:22px;color:var(--navy);letter-spacing:.5px;text-transform:uppercase}
.site-header .brand{left:130px;top:12px}
.nav{position:absolute;left:562px;top:31px;display:flex;gap:42px;font-size:12px;color:var(--ink);letter-spacing:.3px}
.nav .active{color:var(--blue)}
.help{position:absolute;left:940px;top:24px;display:flex;gap:8px;align-items:center}
.help small{display:block;font-size:9px;color:var(--muted)}
.help b{display:block;font-size:11px;color:var(--blue);font-weight:700}

/* buttons */
.pill{position:absolute;display:flex;align-items:center;height:40px;border-radius:20px;background:var(--navy);color:#fff;font-size:11px;font-weight:700;padding:0 22px 0 4px;gap:14px;text-transform:uppercase}
.pill .dot{width:32px;height:32px;border-radius:50%;background:#fff}

/* hero */
.hero-kicker{left:128px;top:218px;font-size:13px}
.hero-title{left:128px;top:240px;font-weight:800;font-size:34px;line-height:39px;color:var(--navy);font-family:"Nunito Sans",sans-serif}

/* section titles */
.kicker{font-size:16px;color:var(--ink)}
.title{font-family:"Raleway",sans-serif;font-weight:500;font-size:35px;line-height:40px;color:var(--navy)}
.para{font-size:12.5px;line-height:20px;color:var(--ink)}

.services-band{left:0;top:1108px;width:1200px;height:605px;background:var(--pale)}
.card{position:absolute;top:1301px;width:300px;height:352px;border-radius:8px;overflow:hidden}
.card-label{position:absolute;left:26px;bottom:58px;color:#fff;font-family:"Raleway",sans-serif;font-size:16px;font-weight:500}
.card-panel{position:absolute;left:28px;top:143px;width:245px;height:166px;background:#fff;border-radius:6px;padding:20px 12px}
.card-panel h4{font-family:"Raleway",sans-serif;font-weight:600;font-size:16px;color:var(--ink);margin:14px 0 10px}
.card-panel p{font-size:10.5px;line-height:17px;color:var(--muted)}

.feature{position:absolute;top:2040px;width:209px;height:88px;border:1px solid #dde4e9;padding:16px 12px 0 48px}
.feature h5{font-size:12px;font-weight:600;color:var(--ink)}
.feature p{font-size:9.5px;line-height:14px;color:var(--muted);margin-top:4px}
.feature svg{position:absolute;left:10px;top:18px}

.how{left:0;top:2335px;width:1200px;height:425px;background:linear-gradient(120deg,#10283a,#1b3a4e 55%,#14303f)}
.how-step{position:absolute;top:2600px;width:300px;text-align:center;color:#fff}
.how-step h3{font-family:"Raleway",sans-serif;font-weight:500;font-size:19px;margin-bottom:14px}
.how-step p{font-size:11.5px;line-height:18px;color:#c8d4dc}

.field{position:absolute;border:1.5px solid var(--navy);font-size:10.5px;color:var(--ink);padding:14px 12px}
.submit{position:absolute;left:605px;top:3021px;width:318px;height:42px;background:var(--blue);color:#fff;font-size:11.5px;font-weight:700;display:flex;align-items:center;justify-content:center;letter-spacing:.5px}

.cta{left:0;top:3137px;width:1200px;height:395px;background:linear-gradient(90deg,#1d2a36,#27394a 60%,#22384b)}
.cta-btn{position:absolute;top:3368px;height:42px;border-radius:21px;display:flex;align-items:center;gap:14px;padding:0 22px 0 4px;color:#fff;font-size:11px;font-weight:700}
.cta-btn .dot{width:34px;height:34px;border-radius:50%;background:#fff}

.footer{left:0;top:3532px;width:1200px;height:387px;background:linear-gradient(90deg,#284c63,#2b5570)}
.footer .brand-name{color:#fff}
.fcol h4{font-family:"Raleway",sans-serif;font-weight:500;font-size:16px;color:#fff;margin-bottom:18px}
.fcol li{list-style:none;font-size:11.5px;color:#e2ebf1;margin-bottom:10px;display:flex;align-items:center;gap:6px}
.fcol li::before{content:"";width:7px;height:7px;border-radius:50%;background:var(--blue-bright)}
.fcontact{position:absolute;left:845px;display:flex;gap:10px;font-size:11px;color:#e2ebf1;line-height:14px}
.fcontact .ic{width:28px;height:28px;border-radius:50%;border:1.5px solid #fff;flex:none;display:flex;align-items:center;justify-content:center}
.social{position:absolute;top:3770px;width:30px;height:30px;border-radius:50%;background:rgba(255,255,255,.18)}
.copy{position:absolute;left:0;top:3876px;width:1200px;text-align:center;font-size:9.5px;color:#e2ebf1}
.copy span{color:var(--blue-bright)}
</style>
</head>
<body>

<header class="site-header">
  <div class="brand"><div class="brand-dot"></div><div class="brand-name">Meridale<br>Partners</div></div>
  <nav class="nav"><span class="active">HOME</span><span>ABOUT US</span><span>SERVICES</span><span>CONTACT US</span></nav>
  <div class="help">
    <svg width="22" height="22" viewBox="0 0 22 22" fill="none" stroke="#2c3a44" stroke-width="1.5"><path d="M4 13V10a7 7 0 0 1 14 0v3"/><rect x="2" y="12" width="4" height="6" rx="1.5"/><rect x="16" y="12" width="4" height="6" rx="1.5"/></svg>
    <div><small>Have Any Questions?</small><b>+ 84 1800 555 210</b></div>
  </div>
</header>

<!-- hero -->
<svg class="abs" style="left:0;top:78px" width="1200" height="456" viewBox="0 0 1200 456">
  <g fill="none" stroke="#e4e8eb" stroke-width="1">
    <path d="M90 456C120 300 300 180 520 220S900 420 1060 590"/>
    <path d="M110 456C150 320 320 210 520 250S880 430 1040 600"/>
    <path d="M400 0C450 120 600 160 700 260"/>
    <path d="M440 0C480 110 620 150 720 240"/>
  </g>
  <polygon points="800,0 1200,0 1200,456 531,456" fill="#3b5566" role="img" aria-label="Photo of a consultant presenting a data analytics dashboard to colleagues"/>
  <polygon points="800,0 1200,0 1200,456 531,456" fill="url(#heroShade)"/>
  <polygon points="756,0 815,0 680,190 636,190" fill="#2a8fd8"/>
  <defs><linearGradient id="heroShade" x1="0" y1="0" x2="1" y2="1"><stop offset="0" stop-color="#2e6a8c" stop-opacity=".6"/><stop offset="1" stop-color="#1c2b36" stop-opacity=".6"/></linearGradient></defs>
</svg>
<div class="abs hero-kicker">Meridale Partners</div>
<h1 class="abs hero-title">DATA ANALYTICS &amp;<br>EPM CONSULTING SERVICES</h1>
<div class="pill" style="left:128px;top:348px"><span class="dot"></span>Explore More</div>

<!-- welcome -->
<div class="abs" role="img" aria-label="Round photo collage of team members working at desks" style="left:132px;top:604px;width:436px;height:436px;border-radius:50%;background:linear-gradient(135deg,#4f8a9a,#2e6b98 45%,#223847)"></div>
<div class="abs kicker" style="left:655px;top:708px">Welcome To</div>
<h2 class="abs title" style="left:655px;top:732px">Meridale Partners</h2>
<p class="abs para" style="left:655px;top:800px;width:420px">MP are a Data Analytics &amp; EPM company, specialising in the implementation and support of Business Intelligence, EPM and Data Analytics business solutions, both in the Cloud and on-premise.</p>
<div class="pill" style="left:655px;top:889px"><span class="dot"></span>Read More</div>

<!-- services -->
<div class="abs services-band"></div>
<div class="abs kicker" style="left:131px;top:1164px">What We Do</div>
<h2 class="abs title" style="left:131px;top:1186px">We Offer Consulting<br>Services</h2>
<p class="abs para" style="left:610px;top:1190px;width:440px">Sed ut perspiciatis unde omnis iste natus error sit voluptatem accusantium doloremque laudantium, totam rem aperiam, eaque ipsa quae ab illo inventore veritatis et quasi architecto...</p>

<div class="card" style="left:130px" role="img" aria-label="Photo of an analyst pointing at charts on a monitor">
  <div style="position:absolute;inset:0;background:linear-gradient(160deg,#2a3c48,#3d4a50 60%,#1f2b33)"></div>
  <svg style="position:absolute;left:26px;top:212px" width="40" height="40" viewBox="0 0 40 40" fill="none" stroke="#fff" stroke-width="1.6"><rect x="4" y="4" width="20" height="16"/><path d="M8 16v-5M13 16v-8M18 16v-3"/><circle cx="28" cy="24" r="5"/><path d="M19 38c0-6 4-9 9-9s9 3 9 9"/></svg>
  <div class="card-label">Advise &amp; Architect Services</div>
</div>
<div class="card" style="left:450px">
  <div role="img" aria-label="Photo of a team member in an office" style="position:absolute;inset:0;background:linear-gradient(160deg,#3b5564,#2b4350 60%,#20323e)"></div>
  <div class="card-panel">
    <svg width="48" height="40" viewBox="0 0 48 40" fill="none" stroke="#2c5d80" stroke-width="1.6"><rect x="2" y="4" width="10" height="8"/><rect x="16" y="14" width="26" height="18" rx="2"/><path d="M7 12v10h9M22 23h14"/><circle cx="10" cy="2" r="1.5"/></svg>
    <h4>Design &amp; Implement</h4>
    <p>Working with the project management team, through each stage of the project, with clearly defined deliverables...</p>
  </div>
</div>
<div class="card" style="left:770px" role="img" aria-label="Photo of two colleagues reviewing documents at a table">
  <div style="position:absolute;inset:0;background:linear-gradient(160deg,#6b6a62,#4e5a60 55%,#34424a)"></div>
  <svg style="position:absolute;left:26px;top:212px" width="40" height="40" viewBox="0 0 40 40" fill="none" stroke="#fff" stroke-width="1.6"><circle cx="20" cy="14" r="10"/><circle cx="20" cy="14" r="4"/><path d="M6 32h12l8-4M6 36h22"/></svg>
  <div class="card-label">Optimise &amp; Manage</div>
</div>

<!-- who we are -->
<div class="abs" style="left:200px;top:1825px;width:340px;height:340px;transform:rotate(45deg);background:linear-gradient(135deg,#eef2f5,#ffffff)"></div>
<div class="abs" role="img" aria-label="Diamond collage of business people collaborating" style="left:226px;top:1851px;width:288px;height:288px;transform:rotate(45deg);background:linear-gradient(135deg,#2c4350,#3b6d7a 50%,#6f8fb0)"></div>
<div class="abs kicker" style="left:641px;top:1850px">Company</div>
<h2 class="abs title" style="left:641px;top:1872px">Who We Are</h2>
<p class="abs para" style="left:641px;top:1938px;width:430px">Sed ut perspiciatis unde omnis iste natus error sit voluptatem accusantium doloremque laudantium, totam rem aperiam, eaque ipsa quae ab illo inventore veritatis et quasi architecto beatae vitae dicta sunt explicabo.</p>
<div class="feature" style="left:641px">
  <svg width="32" height="24" viewBox="0 0 32 24" fill="none" stroke="#2c5d80" stroke-width="1.4"><circle cx="16" cy="6" r="4"/><circle cx="5" cy="14" r="3"/><circle cx="27" cy="14" r="3"/><path d="M9 22c0-5 3-8 7-8s7 3 7 8"/></svg>
  <h5>Experience</h5><p>Our great team of more than 1400 software experts.</p>
</div>
<div class="feature" style="left:862px">
  <svg width="24" height="24" viewBox="0 0 24 24" fill="#2c5d80"><circle cx="12" cy="7" r="5"/><path d="M2 24c0-6 4-10 10-10s10 4 10 10z"/></svg>
  <h5>Quick Support</h5><p>We'll help you test bold new ideas while sharing your.</p>
</div>
<div class="pill" style="left:641px;top:2157px"><span class="dot"></span>Read More</div>

<!-- how we do it -->
<div class="abs how" role="img" aria-label="Dimmed photo of a team meeting"></div>
<h2 class="abs h-font" style="left:0;top:2410px;width:1200px;text-align:center;color:#fff;font-weight:500;font-size:33px">How We Do It</h2>
<p class="abs" style="left:0;top:2462px;width:1200px;text-align:center;color:#dfe8ee;font-size:12.5px">Sed ut perspiciatis unde omnis iste natus error sit voluptatem</p>
<svg class="abs" style="left:240px;top:2520px" width="72" height="60" viewBox="0 0 72 60" fill="none" stroke="#fff" stroke-width="2.4"><path d="M6 10v44M16 20v34M26 10v44M36 24v30M46 14v40M56 22v32M66 18v36"/><path d="M2 6l20 30 14-14 30 30" stroke="#2a8fd8"/></svg>
<svg class="abs" style="left:558px;top:2518px" width="64" height="62" viewBox="0 0 64 62" fill="none" stroke="#fff" stroke-width="2"><rect x="2" y="2" width="24" height="14"/><circle cx="18" cy="32" r="8"/><path d="M4 60c0-10 6-16 14-16s14 6 14 16"/><circle cx="46" cy="24" r="7"/><path d="M34 48c0-8 5-13 12-13s12 5 12 13"/></svg>
<svg class="abs" style="left:886px;top:2520px" width="66" height="58" viewBox="0 0 66 58" fill="none" stroke="#fff" stroke-width="2"><circle cx="24" cy="22" r="16"/><circle cx="24" cy="22" r="7"/><path d="M24 2v6M24 36v6M4 22h6M38 22h6"/><rect x="34" y="26" width="28" height="20" rx="3"/><path d="M40 46l-4 8 10-8M40 34h16M40 39h12"/></svg>
<svg class="abs" style="left:404px;top:2543px" width="400" height="10" viewBox="0 0 400 10" fill="none" stroke="#2a8fd8" stroke-width="1.4"><path d="M0 5h72M66 1l6 4-6 4"/><path d="M320 5h74M388 1l6 4-6 4"/></svg>
<div class="how-step" style="left:129px"><h3>Eiusmod Tempor</h3><p>Sed ut perspiciatis unde omnis iste natus error sit voluptatem accusantium</p></div>
<div class="how-step" style="left:450px"><h3>Tempora Incidunt</h3><p>Sed ut perspiciatis unde omnis iste natus error sit voluptatem accusantium</p></div>
<div class="how-step" style="left:770px"><h3>Finibus Bonorum</h3><p>Sed ut perspiciatis unde omnis iste natus error sit voluptatem accusantium</p></div>

<!-- contact -->
<h2 class="abs h-font" style="left:0;top:2820px;width:1200px;text-align:center;color:var(--navy);font-weight:500;font-size:33px">Contact Us</h2>
<p class="abs" style="left:0;top:2870px;width:1200px;text-align:center;font-size:12.5px">Sed ut perspiciatis unde omnis iste natus error sit voluptatem</p>
<div class="field" style="left:276px;top:2913px;width:319px;height:42px">Name:</div>
<div class="field" style="left:276px;top:2967px;width:319px;height:42px">Email:</div>
<div class="field" style="left:276px;top:3021px;width:319px;height:42px">Phone:</div>
<div class="field" style="left:605px;top:2913px;width:318px;height:96px">Message:</div>
<div class="submit">SUBMIT</div>

<!-- call to action -->
<div class="abs cta" role="img" aria-label="Photo of a smiling professional in an office"></div>
<svg class="abs" style="left:0;top:3137px" width="1200" height="395" viewBox="0 0 1200 395"><polygon points="270,0 430,0 620,230 460,395 300,395 460,230" fill="#1c5fd0" opacity=".85"/><rect x="0" y="0" width="260" height="395" fill="#3a3a3a" opacity=".25"/></svg>
<div class="abs" style="left:669px;top:3195px;color:#fff;font-family:'Raleway',sans-serif;font-size:20px">Contact Us To</div>
<h2 class="abs h-font" style="left:669px;top:3218px;color:#fff;font-weight:500;font-size:33px;line-height:37px">Discuss Your Business<br>Needs</h2>
<div class="abs" style="left:669px;top:3305px;color:#fff;font-size:13px">Advise &amp; Architect | Design &amp; Implement | Optimise &amp; Manage</div>
<div class="cta-btn" style="left:669px;background:var(--orange)"><span class="dot"></span>01 555 0142</div>
<div class="cta-btn" style="left:832px;background:var(--blue-bright)"><span class="dot"></span>CONTACT US</div>

<!-- footer -->
<div class="abs footer"></div>
<div class="brand" style="left:130px;top:3602px"><div class="brand-dot" style="background:#fff;width:54px;height:54px"></div><div class="brand-name">Meridale<br>Partners</div></div>
<p class="abs" style="left:130px;top:3680px;width:220px;font-size:11.5px;line-height:19px;color:#e2ebf1">Meridale Partners is an exciting start-up in the Data Analytics and EPM space.</p>
<div class="social" style="left:132px"></div>
<div class="social" style="left:174px"></div>
<div class="abs fcol" style="left:462px;top:3602px"><h4>Quick Links</h4><ul><li>Home</li><li>About Us</li><li>Services</li><li>Contact Us</li></ul></div>
<div class="abs fcol" style="left:636px;top:3602px"><h4>Services</h4><ul><li>Advise &amp; Architect</li><li>Design &amp; Implement</li><li>Optimise &amp; Manage</li></ul></div>
<div class="abs fcol" style="left:845px;top:3602px"><h4>Contact Us</h4></div>
<div class="fcontact" style="top:3640px"><span class="ic"><svg width="12" height="14" viewBox="0 0 12 14" fill="none" stroke="#fff" stroke-width="1.4"><path d="M6 13S1 8 1 5a5 5 0 0 1 10 0c0 3-5 8-5 8z"/><circle cx="6" cy="5" r="1.6"/></svg></span><span>14 Harbour Row, Northfield,<br>Dublin 4, D04 QX11</span></div>
<div class="fcontact" style="top:3692px;align-items:center"><span class="ic"><svg width="12" height="12" viewBox="0 0 12 12" fill="none" stroke="#fff" stroke-width="1.4"><path d="M2 1h3l1 3-2 1a6 6 0 0 0 3 3l1-2 3 1v3c-6 0-9-3-9-9z"/></svg></span><span>01 555 0142</span></div>
<div class="fcontact" style="top:3745px;align-items:center"><span class="ic"><svg width="12" height="10" viewBox="0 0 12 10" fill="none" stroke="#fff" stroke-width="1.3"><rect x="1" y="1" width="10" height="8"/><path d="M1 1l5 4 5-4"/></svg></span><span>info@meridale-partners.example</span></div>
<div class="abs" style="left:130px;top:3840px;width:940px;height:1px;background:rgba(255,255,255,.2)"></div>
<div class="copy">Copyright © 2022 <span>Brightwell Studio</span>. All Rights Reserved.</div>

</body>
</html>
```